The Linen Loft Co

We need a business card design for our wardrobe company.
Please visit our website www.gentlelinenlofts.com to get an idea of who we are.

```html
<!DOCTYPE html>
<html lang="en">
<head>
<meta charset="utf-8">
<title>The Linen Loft Co — Business Card</title>
<link href="https://fonts.googleapis.com/css2?family=Lato:wght@400;700&family=Montserrat:wght@600&display=swap" rel="stylesheet">
<style>
  :root {
    --backdrop: #2b2b2b;
    --card-front: #ffffff;
    --card-back: #505050;
    --ink: #111111;
    --ink-soft: #1c1c1c;
    --rule: #9a9a9a;
    --rule-light: #d8d8d8;
    --paper-text: #ffffff;
  }
  html, body {
    margin: 0;
    padding: 0;
    width: 1200px;
    height: 1200px;
    overflow: hidden;
    background: var(--backdrop);
  }
  .canvas {
    position: relative;
    width: 1200px;
    height: 1200px;
    font-family: "Lato", sans-serif;
  }
  .card {
    position: absolute;
    top: 310px;
    width: 364px;
    height: 594px;
    box-shadow: 2px 3px 6px rgba(0,0,0,0.5);
  }
  .card-front { left: 234px; background: var(--card-front); color: var(--ink); }
  .card-back { left: 628px; width: 368px; background: var(--card-back); color: var(--paper-text); }

  .brand-mark {
    position: absolute;
    top: 160px;
    left: 0;
    width: 100%;
    text-align: center;
    font-family: "Lato", sans-serif;
    font-weight: 700;
    font-size: 27px;
    letter-spacing: 1px;
    white-space: nowrap;
    color: var(--ink);
  }
  .person-name {
    position: absolute;
    top: 334px;
    left: 0; width: 100%;
    text-align: center;
    font-family: "Montserrat", sans-serif;
    font-weight: 600;
    font-size: 21px;
    letter-spacing: 0.5px;
  }
  .person-role {
    position: absolute;
    top: 360px;
    left: 0; width: 100%;
    text-align: center;
    font-size: 16px;
    color: var(--ink-soft);
  }
  .contact-icons {
    position: absolute;
    top: 396px;
    left: 87px;
    width: 190px;
    height: 24px;
  }
  .contact-lines {
    position: absolute;
    top: 430px;
    left: 0; width: 100%;
    text-align: center;
    font-size: 16px;
    line-height: 22px;
    color: var(--ink-soft);
  }
  .contact-divider {
    position: absolute;
    top: 507px;
    left: 96px;
    width: 175px;
    height: 1px;
    background: var(--rule-light);
  }
  .address {
    position: absolute;
    top: 517px;
    left: 0; width: 100%;
    text-align: center;
    font-size: 16px;
    line-height: 22px;
    color: var(--ink-soft);
  }

  .back-title {
    position: absolute;
    left: 155px;
    top: 64px;
    height: 292px;
    writing-mode: vertical-rl;
    transform: rotate(180deg);
    font-weight: 700;
    font-size: 19px;
    letter-spacing: 0.5px;
    white-space: nowrap;
    text-align: left;
  }
  .back-tagline {
    position: absolute;
    left: 189px;
    top: 104px;
    height: 214px;
    writing-mode: vertical-rl;
    transform: rotate(180deg);
    font-size: 17px;
    white-space: nowrap;
    text-align: left;
  }
  .back-mark {
    position: absolute;
    left: 170px;
    top: 368px;
    height: 160px;
    writing-mode: vertical-rl;
    transform: rotate(180deg);
    font-weight: 700;
    font-size: 15px;
    text-align: center;
    letter-spacing: 0.5px;
    white-space: nowrap;
  }
</style>
</head>
<body>
<main class="canvas">
  <section class="card card-front">
    <div class="brand-mark">THE LINEN LOFT CO</div>
    <div class="person-name">DANIEL HARTLEY</div>
    <div class="person-role">Managing Director</div>
    <svg class="contact-icons" viewBox="0 0 190 24" aria-hidden="true">
      <line x1="0" y1="12" x2="54" y2="12" stroke="var(--rule)" stroke-width="1"/>
      <line x1="136" y1="12" x2="190" y2="12" stroke="var(--rule)" stroke-width="1"/>
      <circle cx="67" cy="12" r="11" fill="var(--ink)"/>
      <path d="M62 8 q0-2 2-2 l2 0 0 3 -1.5 1 q1.5 3 4 4 l1-1.5 3 0 0 2 q0 2-2 2 q-8-1-8.5-8.5z" fill="#fff"/>
      <circle cx="95" cy="12" r="11" fill="var(--ink)"/>
      <rect x="89" y="8" width="12" height="8" fill="#fff"/>
      <path d="M89 8 l6 5 6-5" fill="none" stroke="var(--ink)" stroke-width="1"/>
      <circle cx="123" cy="12" r="11" fill="var(--ink)"/>
      <circle cx="123" cy="12" r="6" fill="none" stroke="#fff" stroke-width="1.4"/>
      <line x1="117" y1="12" x2="129" y2="12" stroke="#fff" stroke-width="1"/>
      <ellipse cx="123" cy="12" rx="2.5" ry="6" fill="none" stroke="#fff" stroke-width="1"/>
    </svg>
    <div class="contact-lines">
      0207 555 0148<br>
      info@gentlelinenlofts.com<br>
      www.gentlelinenlofts.com
    </div>
    <div class="contact-divider"></div>
    <div class="address">
      Ashby House, 42 Mill Lane<br>
      London N1 7QT
    </div>
  </section>

  <section class="card card-back">
    <div class="back-title">THE LINEN LOFT CO</div>
    <div class="back-tagline">Crafted for every corner</div>
    <div class="back-mark">THE LINEN LOFT CO</div>
  </section>
</main>
</body>
</html>
```